Web Developer Needs a Business Card Design

I need a personal business card design that represents me as a web developer for potential employers. I would like the background to be a dark color on the front for contrast with my logo and name. The back will have all my information along with a smaller version of the logo. I want something with a modern look and feel, not too conservative. This will be used for potential employers and freelance work.

Industry/Entity Type

Business

Contact Information for Business Card

Front should have my logo and name. The back should have all my personal information which would include: name: Tom Varulek, phone: 570-614-3098, email: tomvarulek@quillbox.net, website url: www.tomvarulek.net, logo, web developer.

Font styles to use
Sans Serif

Requirements
Must have
• Must include my logo. The color palette base color will be the logo color.

```html
<!DOCTYPE html>
<html lang="en">
<head>
<meta charset="utf-8">
<title>Tom Varulek — Business Card</title>
<link href="https://fonts.googleapis.com/css2?family=Open+Sans:wght@400;600&display=swap" rel="stylesheet">
<style>
  :root {
    --backdrop: #3a3531;
    --card: #0d0d0d;
    --teal: #6ccfb8;
    --silver: #c8c8c8;
    --text-light: #e6e6e6;
    --divider: #2a2a2a;
  }
  * { box-sizing: border-box; margin: 0; padding: 0; }
  html, body { width: 1200px; height: 900px; overflow: hidden; }
  body {
    background: var(--backdrop);
    font-family: "Open Sans", sans-serif;
    position: relative;
  }
  .card {
    position: absolute;
    top: 307px;
    width: 500px;
    height: 286px;
    background: var(--card);
    box-shadow: 0 10px 30px rgba(0,0,0,.45);
  }
  .card-back { left: 60px; display: flex; }
  .card-front { left: 640px; }

  .back-mark {
    width: 236px;
    display: flex;
    align-items: center;
    justify-content: center;
  }
  .divider {
    width: 1px;
    margin: 34px 0;
    background: var(--divider);
  }
  .back-info { padding: 50px 0 0 26px; }
  .holder-name {
    color: var(--teal);
    font-weight: 600;
    font-size: 18px;
    line-height: 1.2;
  }
  .holder-role {
    color: var(--text-light);
    font-size: 13px;
    margin-bottom: 18px;
  }
  .contact-list { list-style: none; }
  .contact-list li {
    display: flex;
    align-items: center;
    gap: 9px;
    color: var(--text-light);
    font-size: 13.5px;
    line-height: 22px;
  }
  .contact-list svg { width: 10px; height: 10px; flex: none; fill: var(--teal); }

  .front-mark {
    position: absolute;
    left: 155px;
    top: 38px;
  }
  .front-name {
    position: absolute;
    left: 0;
    right: 0;
    top: 196px;
    text-align: center;
    color: var(--silver);
    font-weight: 600;
    font-size: 24px;
    padding-left: 70px;
  }
</style>
</head>
<body>
  <section class="card card-back" aria-label="Business card back">
    <div class="back-mark">
      <svg width="168" height="168" viewBox="0 0 168 168" aria-hidden="true">
        <circle cx="84" cy="84" r="77" fill="none" stroke="var(--teal)" stroke-width="12"/>
      </svg>
    </div>
    <div class="divider"></div>
    <div class="back-info">
      <p class="holder-name">Tom Varulek</p>
      <p class="holder-role">Front-End Developer</p>
      <ul class="contact-list">
        <li>
          <svg viewBox="0 0 10 10" aria-hidden="true"><path d="M2 0.5 L3.6 2.6 L2.7 3.6 Q4 6 6.4 7.3 L7.4 6.4 L9.5 8 L8.2 9.5 Q1.5 8 0.5 1.8 Z"/></svg>
          570-614-3098
        </li>
        <li>
          <svg viewBox="0 0 10 10" aria-hidden="true"><path d="M0.5 2 H9.5 V8.5 H0.5 Z M1 2.5 L5 5.6 L9 2.5" stroke="var(--card)" stroke-width="0.8"/></svg>
          tomvarulek@quillbox.net
        </li>
        <li>
          <svg viewBox="0 0 10 10" aria-hidden="true"><circle cx="5" cy="5" r="4.5"/><path d="M0.5 5 H9.5 M5 0.5 V9.5 M1.5 3 H8.5 M1.5 7 H8.5" stroke="var(--card)" stroke-width="0.7" fill="none"/></svg>
          www.tomvarulek.net
        </li>
      </ul>
    </div>
  </section>

  <section class="card card-front" aria-label="Business card front">
    <svg class="front-mark" width="150" height="150" viewBox="0 0 150 150" aria-hidden="true">
      <circle cx="75" cy="75" r="69" fill="none" stroke="var(--silver)" stroke-width="10"/>
    </svg>
    <p class="front-name">Tom Varulek</p>
  </section>
</body>
</html>
```